Business card design for Automotive workshop

We need a business card for a new automotive repair and tyre shop called Keelstone Prime Automotive located in New Zealand. We are a clean, modern and fresh workshop and company.

Front needs to feature logo,
my name:
Marlo Fenwicke (director)

Address:
48 Tarn Lane
Whitianga 3510

Phone: 07 594 2713
Mobile: 027 451 9362
Email: office@keelstoneautomotive.example.nz
Website: keelstoneautomotive.example.nz

Back needs to feature an area to write down appointment details, date and time.

Also feature a list of jobs and work we do such as,
Vehicle Servicing
All Mechanical Repairs
Warrant of Fitness
Tyres & Wheel Alignments
Automotive Diagnostics
Automotive Parts & Supplies

```html
<!DOCTYPE html>
<html lang="en">
<head>
<meta charset="utf-8">
<title>Keelstone Prime Automotive – Business Card</title>
<link href="https://fonts.googleapis.com/css2?family=Open+Sans:wght@400;600;700&display=swap" rel="stylesheet">
<style>
  :root {
    --red: #e3262b;
    --ink: #141414;
    --edge: #1a1a1a;
    --backdrop: #e6e6e8;
  }
  * { box-sizing: border-box; margin: 0; padding: 0; }
  html, body { width: 1200px; height: 900px; overflow: hidden; }
  body {
    background: var(--backdrop);
    font-family: "Open Sans", sans-serif;
    color: var(--ink);
    display: flex;
    flex-direction: column;
    align-items: center;
    justify-content: center;
    gap: 40px;
  }
  .card {
    position: relative;
    width: 700px;
    height: 400px;
    border-radius: 26px;
    overflow: hidden;
    box-shadow: 0 10px 28px rgba(0,0,0,.22);
  }
  .card-art { position: absolute; inset: 0; width: 100%; height: 100%; }
  .brand {
    position: absolute;
    display: flex;
    align-items: center;
    gap: 10px;
    font-weight: 700;
    color: var(--red);
    text-transform: uppercase;
    line-height: 1.1;
    letter-spacing: .5px;
  }
  .brand-mark { width: 13px; height: 13px; background: var(--red); flex: none; }

  /* Back: appointment side */
  .card-back .brand { left: 150px; top: 40px; font-size: 22px; white-space: nowrap; }
  .services {
    position: absolute;
    left: 152px;
    top: 98px;
    list-style: none;
    display: grid;
    grid-template-columns: auto auto;
    column-gap: 24px;
    row-gap: 10px;
    font-size: 15px;
  }
  .services li { white-space: nowrap; }
  .services li::before { content: "•"; color: var(--red); margin-right: 6px; }
  .appointment {
    position: absolute;
    left: 200px;
    top: 262px;
    display: flex;
    gap: 40px;
  }
  .appointment-field {
    width: 170px;
    border-bottom: 1.5px solid var(--ink);
    text-align: right;
    font-size: 18px;
    padding-bottom: 2px;
  }

  /* Front: contact side */
  .card-front .brand { left: 36px; top: 172px; width: 270px; font-size: 22px; }
  .contact {
    position: absolute;
    left: 336px;
    top: 96px;
    padding-left: 14px;
    border-left: 2px solid var(--red);
    font-size: 14px;
    line-height: 1.3;
  }
  .contact-name { font-weight: 700; font-size: 20px; line-height: 1.2; }
  .contact-role { color: var(--red); font-size: 15px; margin-bottom: 12px; }
  .contact-address { font-size: 15px; margin-bottom: 12px; }
  .contact-line { display: flex; align-items: center; gap: 7px; white-space: nowrap; }
  .contact-icon { width: 13px; height: 13px; flex: none; }
</style>
</head>
<body>

<section class="card card-back" aria-label="Card back: services and appointment">
  <svg class="card-art" viewBox="0 0 700 400" preserveAspectRatio="none">
    <defs>
      <linearGradient id="weave-back" x1="0" y1="0" x2="1" y2="1">
        <stop offset="0" stop-color="#f4f4f4"/>
        <stop offset=".5" stop-color="#dedede"/>
        <stop offset="1" stop-color="#ececec"/>
      </linearGradient>
    </defs>
    <rect width="700" height="400" fill="url(#weave-back)" role="img" aria-label="Light silver woven carbon texture"/>
    <path d="M610,-4 H704 V210 L585,118 Q560,100 572,76 Z" fill="var(--red)" stroke="var(--edge)" stroke-width="4"/>
    <path d="M-4,192 L112,200 Q140,204 134,232 L88,404 H-4 Z" fill="var(--red)" stroke="var(--edge)" stroke-width="4"/>
  </svg>
  <div class="brand"><span class="brand-mark"></span>Keelstone Prime Automotive</div>
  <ul class="services">
    <li>Vehicle Servicing</li>
    <li>All Mechanical Repairs</li>
    <li>Warrant of Fitness</li>
    <li>Tyres &amp; Wheel Alignments</li>
    <li>Automotive Diagnostics</li>
    <li>Automotive Parts &amp; Supplies</li>
  </ul>
  <div class="appointment">
    <div class="appointment-field">Time</div>
    <div class="appointment-field">Date</div>
  </div>
</section>

<section class="card card-front" aria-label="Card front: contact details">
  <svg class="card-art" viewBox="0 0 700 400" preserveAspectRatio="none">
    <defs>
      <linearGradient id="weave-front" x1="0" y1="0" x2="1" y2="1">
        <stop offset="0" stop-color="#ececec"/>
        <stop offset=".5" stop-color="#dadada"/>
        <stop offset="1" stop-color="#f2f2f2"/>
      </linearGradient>
    </defs>
    <rect width="700" height="400" fill="url(#weave-front)" role="img" aria-label="Light silver woven carbon texture"/>
    <path d="M-4,-4 H300 L205,128 Q188,150 160,144 L-4,100 Z" fill="var(--red)" stroke="var(--edge)" stroke-width="4"/>
    <path d="M-4,404 V392 L135,266 Q158,246 188,256 L500,404 Z" fill="var(--red)" stroke="var(--edge)" stroke-width="4"/>
  </svg>
  <div class="brand"><span class="brand-mark"></span>Keelstone Prime Automotive</div>
  <div class="contact">
    <p class="contact-name">Marlo Fenwicke</p>
    <p class="contact-role">Managing Director</p>
    <p class="contact-address">48 Tarn Lane<br>Whitianga 3510</p>
    <p class="contact-line">
      <svg class="contact-icon" viewBox="0 0 14 14"><rect x="3.5" y="1" width="7" height="12" rx="1.5" fill="none" stroke="var(--red)" stroke-width="1.5"/></svg>
      + 027 451 9362
    </p>
    <p class="contact-line">
      <svg class="contact-icon" viewBox="0 0 14 14"><path d="M1,5 Q7,0 13,5 L11,7 L9,5.5 L5,5.5 L3,7 Z M3,8 H11 V12 H3 Z" fill="var(--red)"/></svg>
      + 07 594 2713
    </p>
    <p class="contact-line">
      <svg class="contact-icon" viewBox="0 0 14 14"><rect x="1" y="3" width="12" height="8" fill="var(--red)"/><path d="M1,3 L7,8 L13,3" fill="none" stroke="#fff" stroke-width="1"/></svg>
      office@keelstoneautomotive.example.nz
    </p>
    <p class="contact-line">
      <svg class="contact-icon" viewBox="0 0 14 14"><rect x="1" y="2" width="12" height="8" rx="1" fill="none" stroke="var(--red)" stroke-width="1.5"/><path d="M5,12 H9" stroke="var(--red)" stroke-width="1.5"/></svg>
      keelstoneautomotive.example.nz
    </p>
  </div>
</section>

</body>
</html>
```